School Canteen Menu

We operate 30 school canteen/cafes across Melbourne. We are looking to update our old menu to a new attractive design.
We offer a variety of both food and drink and we need to highlight our healthy options. We would like to have a background picture of either salads or healthy sandwiche etc.
We have borken our current menu in catogories according to hot food, cold bar, drinks, ice creams etc.
We would prefer it to be a A4 design but other ideas are welcome.

In summary we need a vibrant attractive applealing design.
My business card with our lgo is also attached
Regards

Bram

We have two types of menu a secondary menu for students 12-18 and a primary school menu 5-12 year olds. I have attached samples of both.

Reason: Extended deadline as the director of business is away till sunday

Target Market(s)

12 year old to 18 year olds. School Students. As well as Teachers. Prehaps encouraging Teaches with our Freshly made salads will be a feature.

Industry/Entity Type

School

Requirements
Must have
• Viabrant Colors. Greens, Purples, Yellows.
Should not have
• Red Colors. Considered to be a unhealthy color.

```html
<!DOCTYPE html>
<html lang="en">
<head>
<meta charset="utf-8">
<title>Canteen Menu 2012</title>
<link href="https://fonts.googleapis.com/css2?family=PT+Sans:ital,wght@0,400;0,700;1,700&display=swap" rel="stylesheet">
<style>
  :root {
    --plum: #9c246f;
    --plum-text: #8e2a70;
    --blue-sub: #1d5d97;
    --white: #ffffff;
    --veil: rgba(255,255,255,0.72);
  }
  * { box-sizing: border-box; margin: 0; padding: 0; }
  html, body { width: 848px; height: 1200px; overflow: hidden; background: var(--white); }
  body { font-family: "PT Sans", Arial, sans-serif; color: var(--plum-text); }
  .menu { position: relative; width: 848px; height: 1200px; overflow: hidden; }
  .salad-backdrop {
    position: absolute; left: 0; top: 79px; width: 848px; height: 1074px;
    background:
      radial-gradient(ellipse 260px 200px at 430px 260px, #f2a07e 0%, transparent 70%),
      radial-gradient(ellipse 300px 240px at 700px 500px, #e9865f 0%, transparent 70%),
      radial-gradient(ellipse 320px 260px at 160px 820px, #b9c97a 0%, transparent 70%),
      radial-gradient(ellipse 300px 260px at 620px 860px, #d6b48c 0%, transparent 70%),
      linear-gradient(160deg, #cfd99a 0%, #e8c3a0 40%, #c8d88a 70%, #e3c9a6 100%);
  }
  .salad-backdrop::after { content: ""; position: absolute; inset: 0; background: var(--veil); }
  .masthead {
    position: absolute; left: 0; top: 0; width: 848px; height: 79px;
    background: var(--plum); color: var(--white);
    display: flex; align-items: center; justify-content: center;
  }
  .masthead h1 { font-size: 35px; font-weight: 700; letter-spacing: 0.3px; }
  .footer {
    position: absolute; left: 0; top: 1153px; width: 848px; height: 47px;
    background: var(--plum); color: var(--white);
    display: flex; align-items: center; justify-content: center; gap: 18px;
    font-size: 19px; font-weight: 700;
  }
  .section { position: absolute; width: 355px; }
  .col-left { left: 36px; }
  .col-right { left: 446px; }
  .section-bar {
    background: var(--plum); color: var(--white);
    height: 27px; line-height: 27px; padding-left: 8px;
    font-size: 15.5px; font-weight: 700; letter-spacing: 0.2px;
    margin-bottom: 8px;
  }
  .subhead { color: var(--blue-sub); font-style: italic; font-weight: 700; font-size: 15.5px; margin: 0 0 8px 8px; line-height: 20px; }
  .items { list-style: none; padding-left: 8px; font-size: 15.5px; line-height: 20.6px; }
  .items li { display: grid; grid-template-columns: 1fr 48px; align-items: end; }
  .items li.gap { margin-top: 4px; }
  .price { text-align: left; }
  .note { padding-left: 8px; font-size: 15.5px; line-height: 20.6px; }
  .special { display: grid; grid-template-columns: 1fr 48px; padding-left: 8px; font-size: 15.5px; line-height: 20.6px; }
  .special .subhead { margin: 0; }
</style>
</head>
<body>
<main class="menu">
  <div class="salad-backdrop" role="img" aria-label="Soft background photo of a fresh salad with tomato, lettuce and vegetables"></div>

  <header class="masthead"><h1>Canteen Menu 2012</h1></header>

  <section class="section col-left" style="top:104px">
    <h2 class="section-bar">HOT FOOD</h2>
    <p class="subhead">Jaffles</p>
    <ul class="items">
      <li><span>Cheese</span><span class="price">$2.50</span></li>
      <li><span>Spaghetti</span><span class="price">$2.50</span></li>
      <li><span>Baked Beans</span><span class="price">$2.50</span></li>
      <li><span>Ham &amp; Cheese</span><span class="price">$2.60</span></li>
      <li><span>Ham, Cheese &amp; Pineapple</span><span class="price">$3.00</span></li>
      <li class="gap"><span>Lasagne 97% Fat Free</span><span class="price">$3.60</span></li>
      <li><span>Macaroni &amp; Cheese 97% Fat Free</span><span class="price">$3.60</span></li>
      <li><span>Meat Pie</span><span class="price">$3.20</span></li>
      <li><span>Party Pie or Party Sausage Roll</span><span class="price">$1.00</span></li>
      <li><span>Sausage Roll</span><span class="price">$3.00</span></li>
      <li class="gap"><span>Flame Grilled Beef Burger with lettuce,<br>cheese and tomato</span><span class="price">$4.00</span></li>
      <li class="gap"><span>Chicken Burger<br>with lettuce, cheese &amp; mayonnaise</span><span class="price">$4.00</span></li>
      <li class="gap"><span>Baked Chicken Schnitzel Roll<br>with lettuce, cheese, tomato &amp; mayo</span><span class="price">$4.20</span></li>
      <li class="gap"><span>Corn Cobette</span><span class="price">$1.20</span></li>
      <li><span>Noodles - Chicken or Beef</span><span class="price">$2.60</span></li>
      <li><span>Chicken Nuggets 80c each (3)</span><span class="price">$2.20</span></li>
      <li><span>Steamed Dim Sim</span><span class="price">$0.90</span></li>
      <li><span>Hot Dog</span><span class="price">$3.00</span></li>
    </ul>
  </section>

  <section class="section col-left" style="top:661px">
    <h2 class="section-bar">SPECIALS</h2>
    <div class="special"><p class="subhead">Health Pack 1</p><span class="price">$6.00</span></div>
    <p class="note">Salad Roll, Cookie &amp; 200ml Fruit Box</p>
    <div class="special" style="margin-top:8px"><p class="subhead">Health Pack 2</p><span class="price">$6.00</span></div>
    <p class="note" style="margin-top:8px">Any 97% Fat Free Pasta,300ml Flavoured<br>Milk(FRESH)</p>
  </section>

  <section class="section col-left" style="top:866px">
    <h2 class="section-bar">SALAD PLATES</h2>
    <p class="note">Salad Plates<br>all with lettuce, cucumber, carrot,<br>tomato &amp; beetroot</p>
    <ul class="items" style="margin-top:12px">
      <li><span>Salad</span><span class="price">$3.40</span></li>
      <li><span>Egg</span><span class="price">$3.60</span></li>
      <li><span>Chicken</span><span class="price">$3.90</span></li>
      <li><span>Cheese</span><span class="price">$3.60</span></li>
      <li><span>Ham</span><span class="price">$3.60</span></li>
      <li><span>Tuna</span><span class="price">$3.60</span></li>
    </ul>
  </section>

  <section class="section col-right" style="top:104px">
    <h2 class="section-bar">SANDWICHES</h2>
    <p class="subhead">Sandwiches Rolls 60c extra</p>
    <ul class="items">
      <li><span>Salad &nbsp;&nbsp;lettuce, tomato, carrot,<br>beetroot, cucumber</span><span class="price">$2.80</span></li>
      <li><span>Ham &amp; Tomato</span><span class="price">$2.40</span></li>
      <li><span>Ham, Cheese &amp; Tomato</span><span class="price">$2.60</span></li>
      <li><span>Cheese &amp; Tomato</span><span class="price">$2.40</span></li>
      <li><span>Cheese &amp; Salad</span><span class="price">$3.00</span></li>
      <li><span>Egg &amp; Lettuce</span><span class="price">$2.80</span></li>
      <li><span>Chicken &amp; Salad</span><span class="price">$3.10</span></li>
      <li><span>Tuna &amp; Tomato</span><span class="price">$2.90</span></li>
      <li><span>Tuna, Lettuce &amp; Mayonnaise</span><span class="price">$3.00</span></li>
      <li><span>Yeast Spread</span><span class="price">$1.60</span></li>
      <li><span>Ham</span><span class="price">$2.20</span></li>
      <li class="gap"><span>extra fillings</span><span class="price">$0.40</span></li>
    </ul>
  </section>

  <section class="section col-right" style="top:460px">
    <h2 class="section-bar">WRAPS</h2>
    <p class="subhead" style="margin-bottom:0">BBQ Chicken</p>
    <ul class="items"><li><span>Chicken, Lettuce, BBQ Sauce</span><span class="price">$3.60</span></li></ul>
    <p class="subhead" style="margin:6px 0 0 8px">Sweet Chilli Chicken</p>
    <ul class="items"><li><span>Chicken, Lettuce, Sweet Chilli Sauce</span><span class="price">$3.60</span></li></ul>
  </section>

  <section class="section col-right" style="top:613px">
    <h2 class="section-bar">SNACKS</h2>
    <ul class="items">
      <li><span>Pikelets</span><span class="price">$0.80</span></li>
      <li><span>Pop Corn</span><span class="price">$2.00</span></li>
      <li><span>Fruit Salad – small</span><span class="price">$1.50</span></li>
      <li><span>Fruit of the day</span><span class="price">$0.80</span></li>
      <li><span>Jelly Cup with Fruit</span><span class="price">$1.50</span></li>
      <li><span>Anzac Cookie</span><span class="price">$2.00</span></li>
      <li><span>Mini Muffins (home baked)</span><span class="price">$0.80</span></li>
    </ul>
  </section>

  <section class="section col-right" style="top:815px">
    <h2 class="section-bar">DRINKS</h2>
    <ul class="items">
      <li><span>Flavoured Milk (3000ml) Chocolate,<br>Strawberry, Iced Coffee (FRESH)</span><span class="price">$2.50</span></li>
      <li class="gap"><span>Water (600ml)</span><span class="price">$2.30</span></li>
      <li class="gap"><span>Fruit Juice (200ml) Tropical,<br>Orange, Apple</span><span class="price">$1.5</span></li>
    </ul>
  </section>

  <section class="section col-right" style="top:982px">
    <h2 class="section-bar">ICE CREAMS</h2>
    <ul class="items">
      <li><span>Frozen Orange Wedge</span><span class="price">$0.20</span></li>
      <li><span>Frozen Pineapple Ring</span><span class="price">$0.50</span></li>
      <li><span>Frozen Fruit Yoghurt</span><span class="price">$2.00</span></li>
      <li><span>Ice Pop Tube</span><span class="price">$0.80</span></li>
      <li><span>Frosty Pyramid_Orange, Lemonade</span><span class="price">$2.00</span></li>
    </ul>
  </section>

  <footer class="footer">
    <span>freshbitecanteens.com.au</span><span>|</span><span>P.O Box 418 Northcote, VIC 3070</span>
  </footer>
</main>
</body>
</html>
```